Brivo Hair

Hello - our company Vantor 4 develops novel products for the skin, & hair care industry as well as dietary supplements. We're looking for a label design for a new product. The product is a premium hair loss/growth supplement. Our primary demo is women ages 45-65. I attached the brand logo & some competitive product designs that we find attractive.

I've been traveling & have not had the time to adequately review the designs, please be patient with me.

```html
<!DOCTYPE html>
<html lang="en">
<head>
<meta charset="utf-8">
<title>Brivo Hair – Advanced Hair Regrowth Liquid Label</title>
<link rel="stylesheet" href="https://fonts.googleapis.com/css2?family=Cinzel:wght@700&family=Montserrat:wght@700&family=Rajdhani:wght@500;700&display=swap">
<style>
  :root {
    --stage: #3a3a3a;
    --label-black: #000000;
    --blue-deep: #0a3c9e;
    --blue-mid: #1a6fd0;
    --blue-bright: #29abf2;
    --silver-dark: #9c9c9c;
    --silver-light: #f2f2f2;
    --brand-grey: #96a3b0;
    --brand-blue: #5bb0e6;
    --white: #ffffff;
    --ink: #111111;
    --herb-green: #3a9a3c;
    --mesh-grey: #2c2c2c;
  }
  html, body {
    margin: 0;
    padding: 0;
    width: 900px;
    height: 1200px;
    overflow: hidden;
    background: var(--stage);
  }
  .label {
    position: absolute;
    left: 0;
    top: 17px;
    width: 900px;
    height: 1166px;
    display: block;
  }
  .brand-name { font-family: "Montserrat", sans-serif; font-weight: 700; fill: var(--white); }
  .tagline { font-family: "Montserrat", sans-serif; font-weight: 700; fill: var(--white); letter-spacing: 2px; }
  .product-name { font-family: "Montserrat", sans-serif; font-weight: 700; fill: var(--brand-blue); letter-spacing: 4px; }
  .extract-line { font-family: "Cinzel", serif; font-weight: 700; fill: var(--ink); letter-spacing: 6px; }
  .headline { font-family: "Cinzel", serif; font-weight: 700; fill: var(--white); }
  .subhead { font-family: "Cinzel", serif; font-weight: 700; fill: var(--white); }
  .ingredient { font-family: "Rajdhani", sans-serif; font-weight: 500; fill: var(--white); }
  .footer-line { font-family: "Rajdhani", sans-serif; font-weight: 700; fill: var(--white); letter-spacing: 3px; }
</style>
</head>
<body>
<svg class="label" viewBox="0 0 984 1275" xmlns="http://www.w3.org/2000/svg" aria-label="Brivo Hair supplement label">
  <defs>
    <linearGradient id="blueSweep" x1="0" x2="1" y1="0" y2="0">
      <stop offset="0" stop-color="var(--blue-deep)"/>
      <stop offset="0.5" stop-color="var(--blue-bright)"/>
      <stop offset="1" stop-color="var(--blue-deep)"/>
    </linearGradient>
    <linearGradient id="silverSweep" x1="0" x2="1" y1="0" y2="0">
      <stop offset="0" stop-color="var(--silver-dark)"/>
      <stop offset="0.5" stop-color="var(--silver-light)"/>
      <stop offset="1" stop-color="var(--silver-dark)"/>
    </linearGradient>
    <radialGradient id="meshGlow" cx="0.5" cy="0.5" r="0.6">
      <stop offset="0" stop-color="#3a3a3a"/>
      <stop offset="1" stop-color="var(--label-black)"/>
    </radialGradient>
    <radialGradient id="herbGlow" cx="0.5" cy="0.55" r="0.55">
      <stop offset="0" stop-color="var(--herb-green)"/>
      <stop offset="1" stop-color="#1d5a22"/>
    </radialGradient>
  </defs>

  <!-- base -->
  <rect class="label-base" width="984" height="1275" fill="var(--label-black)"/>

  <!-- header band with chevron -->
  <path class="header-chevron-edge" d="M0 208 H160 L195 266 L492 349 L790 266 L825 208 H984 V222 H832 L797 280 L492 357 L187 280 L152 222 H0 Z" fill="url(#silverSweep)"/>
  <path class="header-band" d="M0 0 H984 V212 H822 L790 272 L492 345 L195 272 L162 212 H0 Z" fill="url(#blueSweep)"/>

  <text class="brand-name" x="492" y="172" text-anchor="middle" font-size="66">Vantor 4</text>
  <text class="tagline" x="492" y="251" text-anchor="middle" font-size="30">CLINICAL STRENGTH</text>

  <!-- product name -->
  <text class="product-name" x="492" y="540" text-anchor="middle" font-size="118">Brivo Hair</text>

  <!-- extract band -->
  <rect class="extract-band" x="0" y="628" width="984" height="78" fill="url(#silverSweep)"/>
  <text class="extract-line" x="492" y="681" text-anchor="middle" font-size="36">HE SHOU WU 12:1 EXTRACT</text>

  <!-- headline band -->
  <path class="headline-band" d="M0 706 H984 V830 H876 L820 920 H165 L108 830 H0 Z" fill="url(#blueSweep)"/>
  <text class="headline" x="492" y="812" text-anchor="middle" font-size="88">ADVANCED</text>
  <text class="subhead" x="492" y="872" text-anchor="middle" font-size="40">HAIR REGROWTH LIQUID</text>

  <!-- herbal illustration area -->
  <rect class="herb-illustration" x="175" y="968" width="168" height="176" rx="60" fill="url(#herbGlow)" role="img" aria-label="Green herbal mortar and pestle with leaves"/>

  <!-- hair follicle network illustration area -->
  <rect class="follicle-illustration" x="455" y="920" width="430" height="275" fill="url(#meshGlow)" role="img" aria-label="Hair follicle drawn as a connected node network"/>

  <!-- ingredients -->
  <rect class="ingredient-rule" x="368" y="978" width="3" height="72" fill="var(--brand-blue)"/>
  <text class="ingredient" x="385" y="1003" font-size="32">Biotin</text>
  <text class="ingredient" x="385" y="1042" font-size="32">10,000 mcg</text>
  <rect class="ingredient-rule" x="368" y="1075" width="3" height="72" fill="var(--brand-blue)"/>
  <text class="ingredient" x="385" y="1100" font-size="32">Collagen</text>
  <text class="ingredient" x="385" y="1140" font-size="32">10,000 mcg</text>

  <!-- footer band -->
  <rect class="footer-edge" x="0" y="1193" width="984" height="5" fill="url(#silverSweep)"/>
  <rect class="footer-band" x="0" y="1198" width="984" height="77" fill="url(#blueSweep)"/>
  <text class="footer-line" x="492" y="1246" text-anchor="middle" font-size="36">HAIR GROWTH LIQUID DROPS</text>
</svg>
</body>
</html>
```